Website Design for Hulls for Heroes

Please design and code a new website.
Here are the sites I like best:
http://www.sailbrisk.com/alternate/
http://www.wheelsforhonor.org
Please make it similar. This is NOT a car donation site. It's a boat donation site. I just like this sites above as a lead generation sites.
Old site:
http://hullsforheroes.org
Updates
Coding
Coded - Design and coding required
Number of Pages Required
1 page
Look and feel
Each slider illustrates characteristics of the customer's brand and the style your logo design should communicate.

```html
<!DOCTYPE html>
<html lang="en">
<head>
<meta charset="utf-8">
<title>Hulls for Heroes – Donate Your Boat</title>
<link href="https://fonts.googleapis.com/css2?family=Lato:wght@400;700;900&display=swap" rel="stylesheet">
<style>
:root{
  --navy:#0d2a7a;
  --navy-deep:#0a1f5c;
  --red:#a3180f;
  --red-dark:#8a130c;
  --gold:#c9a86a;
  --ink:#1c2440;
  --text:#333a4d;
  --muted:#f2f2f2;
  --line:#cfd3dc;
  --white:#ffffff;
}
*{box-sizing:border-box;margin:0;padding:0}
html,body{width:1200px;height:2679px;overflow:hidden}
body{font-family:"Lato",Arial,sans-serif;color:var(--text);background:var(--white);position:relative}
a{color:inherit;text-decoration:none}

/* header */
.site-header{position:absolute;top:0;left:0;width:1200px;height:157px;
  background:linear-gradient(90deg,#0b1c4d 0%,#3b1a2c 45%,#7a1a1c 70%,#1a2a5a 100%)}
.brand{position:absolute;left:40px;top:52px;display:flex;align-items:center;gap:14px}
.brand-dot{width:40px;height:40px;border-radius:50%;background:var(--white)}
.brand-name{font-weight:900;font-size:30px;color:var(--gold);letter-spacing:.5px}
.call-box{position:absolute;left:780px;top:0;width:386px;height:157px;background:var(--navy);
  display:flex;align-items:center;padding-left:34px;gap:18px;color:var(--white)}
.call-icon{width:66px;height:66px;border:3px solid var(--white);border-radius:50%;display:flex;align-items:center;justify-content:center}
.call-text .label{font-weight:900;font-size:21px;line-height:1}
.call-text .number{font-weight:900;font-size:32px;line-height:1.1}
.call-text .hours{font-weight:700;font-size:13px}

.main-nav{position:absolute;top:157px;left:0;width:1200px;height:48px;background:var(--navy)}
.main-nav a{position:absolute;top:13px;color:var(--white);font-weight:900;font-size:16px}

/* hero */
.hero-visual{position:absolute;top:205px;left:0;width:800px;height:395px;
  background:linear-gradient(100deg,#6b6a48 0%,#a09a7e 22%,#e4e6ea 45%,#f4f5f7 70%,#dfe3ea 100%)}
.donate-form{position:absolute;left:795px;top:155px;width:359px;height:445px;background:var(--red)}
.form-head{position:absolute;top:4px;left:-16px;width:390px;height:46px;background:var(--white);
  display:flex;align-items:center;justify-content:center;font-weight:900;font-size:20px;color:var(--red)}
.form-head-badge{position:absolute;top:-18px;left:183px;width:24px;height:22px;border-radius:50%;background:var(--red)}
.form-sub{position:absolute;top:70px;width:100%;text-align:center;color:var(--white);font-weight:900;font-size:16px}
.field{position:absolute;height:30px;background:var(--white);font-size:12px;font-weight:700;color:var(--ink);padding:8px 7px}
.field.select::after{content:"";position:absolute;right:8px;top:12px;border:6px solid transparent;border-top:7px solid #555}
.field.select::before{content:"";position:absolute;right:28px;top:0;width:1px;height:30px;background:var(--line)}
.btn-donate{position:absolute;left:20px;top:375px;width:155px;height:42px;background:var(--navy);
  color:var(--white);font-weight:900;font-size:16px;display:flex;align-items:center;justify-content:center}

/* promise band */
.promise-band{position:absolute;top:600px;left:0;width:1200px;height:218px;background:var(--navy)}
.promise-band::after{content:"";position:absolute;left:0;bottom:-14px;width:1200px;height:14px;background:linear-gradient(#9aa3b8,transparent);opacity:.4}
.promise-title{position:absolute;left:0;top:0;width:540px;height:218px;background:var(--red);
  clip-path:polygon(0 0,440px 0,535px 218px,0 218px);padding:30px 0 0 60px;color:var(--white)}
.promise-title .line{font-weight:900;font-size:27px}
.promise-title .big{font-weight:900;font-size:64px;color:var(--gold);letter-spacing:2px;line-height:1.05}
.promise-item{position:absolute;top:46px;width:150px;text-align:center;color:var(--white);font-weight:900;font-size:14px;line-height:1.25}
.promise-item svg{display:block;margin:0 auto 14px}

/* section titles */
.section-title{position:absolute;left:0;width:1200px;text-align:center;font-weight:900;font-size:30px;color:var(--navy-deep)}
.section-title span{color:var(--red)}
.title-rule{position:absolute;height:1px;background:var(--line)}

/* how */
.step{position:absolute;top:952px;width:310px}
.step svg{position:absolute;left:0;top:0}
.step h3{position:absolute;font-weight:900;font-size:15px;color:var(--navy-deep);line-height:1.25}
.step p{position:absolute;font-weight:700;font-size:14px;color:var(--ink);line-height:1.45}

/* why */
.why-section{position:absolute;top:1157px;left:0;width:1200px;height:415px;
  background:linear-gradient(90deg,#eceeef 0%,#e6e3e1 40%,#d8d5d2 75%,#cfcbc6 100%)}
.why-list{position:absolute;left:140px;top:136px;list-style:none}
.why-list li{display:flex;align-items:center;height:33px;font-size:14px;color:var(--ink)}
.why-list li b{font-weight:900;margin-right:4px}
.arrow-dot{width:24px;height:24px;border-radius:50%;background:var(--red);margin-right:14px;flex:none;display:flex;align-items:center;justify-content:center}

/* faq */
.faq-visual{position:absolute;left:80px;top:1702px;width:520px;height:428px;
  background:linear-gradient(170deg,#8c1b22 0%,#c9c3c4 35%,#3a4a7a 55%,#7d7457 80%,#5a523c 100%)}
.faq-list{position:absolute;left:632px;top:1702px;width:490px}
.faq-item{position:absolute;left:0;width:490px;border:1px solid var(--line);border-radius:10px;background:var(--white);
  padding:0 16px;font-weight:900;font-size:15px;color:var(--ink)}
.faq-item .q{height:40px;display:flex;align-items:center;justify-content:space-between}
.faq-item .a{font-weight:400;font-size:14px;line-height:1.45;color:#444;margin-top:-4px}

/* footer */
.site-footer{position:absolute;top:2188px;left:0;width:1200px;height:464px;
  background:linear-gradient(180deg,#0d2f8a 0%,#0b2575 100%)}
.footer-tab{position:absolute;top:-34px;left:370px;width:460px;height:70px;background:#0d2f8a;border-radius:40px 40px 0 0}
.footer-brand{position:absolute;top:-14px;left:410px;display:flex;align-items:center;gap:14px}
.footer-col{position:absolute;top:170px;color:var(--white)}
.footer-col h4{font-weight:900;font-size:15px;padding-bottom:12px;border-bottom:1px solid rgba(255,255,255,.3);margin-bottom:18px}
.footer-col p{font-weight:700;font-size:12px;line-height:1.5;width:230px}
.footer-col a{display:block;font-weight:700;font-size:13px;line-height:1.45}
.seal{background:#e9ecf2;border-radius:4px;margin-bottom:10px}
.footer-call{position:absolute;left:780px;top:120px;width:350px;height:148px;border:2px solid var(--white);border-radius:6px;
  display:flex;align-items:center;padding-left:26px;gap:16px;color:var(--white)}
.copyright{position:absolute;top:2652px;left:0;width:1200px;height:27px;text-align:center;font-weight:900;font-size:11px;color:var(--ink);padding-top:8px}
</style>
</head>
<body>

<header class="site-header">
  <div class="brand"><span class="brand-dot"></span><span class="brand-name">HULLS FOR HEROES</span></div>
  <a class="call-box" href="tel:18005550142">
    <span class="call-icon"><svg width="34" height="34" viewBox="0 0 24 24"><path fill="#fff" d="M6.6 10.8c1.4 2.8 3.8 5.1 6.6 6.6l2.2-2.2c.3-.3.7-.4 1-.2 1.1.4 2.3.6 3.6.6.6 0 1 .4 1 1V20c0 .6-.4 1-1 1C10.6 21 3 13.4 3 4c0-.6.4-1 1-1h3.5c.6 0 1 .4 1 1 0 1.3.2 2.5.6 3.6.1.3 0 .7-.2 1z"/></svg></span>
    <span class="call-text"><span class="label">CALL TODAY TO DONATE</span><br><span class="number">1-800-555-0142</span><br><span class="hours">Live Operators Available - 7 Days A Week</span></span>
  </a>
</header>

<nav class="main-nav">
  <a href="#how" style="left:178px">HOW TO DONATE</a>
  <a href="#why" style="left:365px">WHY DONATE</a>
  <a href="#faq" style="left:523px">FAQ</a>
  <a href="#about" style="left:610px">ABOUT</a>
</nav>

<div class="hero-visual" role="img" aria-label="Photo of a soldier hugging a young girl holding a small flag, beside a white motor yacht in front of a city skyline"></div>

<form class="donate-form">
  <div class="form-head"><span class="form-head-badge"></span>DONATE YOUR BOATS ONLINE</div>
  <div class="form-sub">Full Tax Deduction - Running or Not</div>
  <div class="field" style="left:17px;top:104px;width:157px">First Name</div>
  <div class="field" style="left:182px;top:104px;width:157px">Last Name</div>
  <div class="field" style="left:17px;top:142px;width:157px">Daytime Phone</div>
  <div class="field" style="left:182px;top:142px;width:157px">Email</div>
  <div class="field" style="left:17px;top:180px;width:322px">Pickup Address</div>
  <div class="field" style="left:17px;top:218px;width:322px">Pickup City</div>
  <div class="field select" style="left:17px;top:256px;width:157px">Pickup State</div>
  <div class="field" style="left:182px;top:256px;width:157px">Zip Code</div>
  <div class="field select" style="left:17px;top:294px;width:157px">Choose Year</div>
  <div class="field select" style="left:182px;top:294px;width:157px">Choose Make</div>
  <div class="field" style="left:17px;top:332px;width:322px">Vehicle Model</div>
  <button class="btn-donate" type="button" style="border:0;top:375px">DONATE NOW</button>
</form>

<section class="promise-band">
  <div class="promise-title">
    <div class="line">DONATE YOUR BOATS TO</div>
    <div class="big">VETERANS</div>
    <div class="line">MAKE A DIFFERENCE</div>
  </div>
  <div class="promise-item" style="left:565px">
    <svg width="60" height="60" viewBox="0 0 60 60"><circle cx="30" cy="30" r="26" fill="none" stroke="#fff" stroke-width="3.5"/><path d="M18 31l9 9 17-20" fill="none" stroke="#fff" stroke-width="4"/></svg>
    You have<br>no costs</div>
  <div class="promise-item" style="left:705px">
    <svg width="60" height="60" viewBox="0 0 60 60"><path d="M4 36h52l-8 10H12z" fill="#fff"/><path d="M18 36V26h18l6 10" fill="#fff"/><rect x="22" y="29" width="5" height="4" fill="#0d2a7a"/><rect x="30" y="29" width="5" height="4" fill="#0d2a7a"/></svg>
    Free pickup,<br>running or not</div>
  <div class="promise-item" style="left:855px">
    <svg width="60" height="60" viewBox="0 0 60 60"><rect x="14" y="4" width="32" height="52" fill="none" stroke="#fff" stroke-width="3"/><text x="30" y="32" text-anchor="middle" fill="#fff" font-size="16" font-weight="900" font-family="Lato,sans-serif">$</text><path d="M20 40h20M20 46h20" stroke="#fff" stroke-width="2.5"/></svg>
    We issue you an<br>IRS tax receipt</div>
  <div class="promise-item" style="left:1005px">
    <svg width="60" height="60" viewBox="0 0 60 60"><rect x="18" y="8" width="32" height="44" fill="none" stroke="#fff" stroke-width="3"/><circle cx="20" cy="32" r="11" fill="#0d2a7a" stroke="#fff" stroke-width="3"/><path d="M12 40l-6 8" stroke="#fff" stroke-width="4"/><path d="M28 16h16M34 24h10M34 40h10" stroke="#fff" stroke-width="2.5"/></svg>
    We take care of<br>all paperwork.</div>
</section>

<section id="how">
  <span class="title-rule" style="left:408px;top:890px;width:60px"></span>
  <h2 class="section-title" style="top:872px">HOW TO <span>DONATE</span></h2>
  <span class="title-rule" style="left:745px;top:890px;width:95px"></span>

  <div class="step" style="left:78px">
    <svg width="58" height="80" viewBox="0 0 58 80"><rect x="4" y="0" width="50" height="9" fill="#0d2a7a"/><rect x="4" y="18" width="14" height="9" fill="#0d2a7a"/><rect x="24" y="18" width="30" height="9" fill="#0d2a7a"/><rect x="4" y="36" width="50" height="9" fill="#0d2a7a"/><path d="M0 76l18-18v8h10v-8z" fill="#0d2a7a"/></svg>
    <h3 style="left:82px;top:38px;width:240px">CALL US AT 1-800-555-0142 OR FILL OUT THE ONLINE FORM</h3>
    <p style="left:82px;top:84px;width:240px">Donating your boat is easy and donation is accepted nationwide.</p>
  </div>
  <div class="step" style="left:447px">
    <svg width="68" height="50" viewBox="0 0 68 50"><path d="M2 24h64l-10 14H12z" fill="#a3180f"/><path d="M18 24V12h22l8 12" fill="#a3180f"/><rect x="23" y="15" width="6" height="5" fill="#fff"/><rect x="32" y="15" width="6" height="5" fill="#fff"/></svg>
    <h3 style="left:105px;top:38px;width:220px">WE PICK UP THE BOAT</h3>
    <p style="left:105px;top:70px;width:230px">Any boats is accepted and we will arrange to pick up your boat when it is most convenient for you.</p>
  </div>
  <div class="step" style="left:845px">
    <svg width="66" height="74" viewBox="0 0 66 74"><rect x="2" y="2" width="58" height="66" fill="none" stroke="#0d2a7a" stroke-width="3"/><rect x="16" y="8" width="34" height="36" fill="none" stroke="#0d2a7a" stroke-width="3"/><text x="33" y="34" text-anchor="middle" fill="#0d2a7a" font-size="22" font-weight="900" font-family="Lato,sans-serif">$</text><path d="M16 52h34M16 60h34" stroke="#0d2a7a" stroke-width="3"/></svg>
    <h3 style="left:96px;top:38px;width:220px">TAX WRITE-OFF</h3>
    <p style="left:96px;top:70px;width:230px">Once the boat donation is complete, you will receive your tax deductable boat donation receipt.</p>
  </div>
</section>

<section class="why-section" id="why">
  <h2 class="section-title" style="top:58px">WHY DONATE <span>YOUR BOATS TO US</span></h2>
  <ul class="why-list">
    <li><span class="arrow-dot"><svg width="12" height="12" viewBox="0 0 12 12"><path d="M1 6h9M6 2l4 4-4 4" stroke="#fff" stroke-width="2" fill="none"/></svg></span><b>A+ Rated &amp; IRS 501(c)3 Approved :</b> Free 24/7 Pickup with No DMV Hassles.</li>
    <li><span class="arrow-dot"><svg width="12" height="12" viewBox="0 0 12 12"><path d="M1 6h9M6 2l4 4-4 4" stroke="#fff" stroke-width="2" fill="none"/></svg></span><b>Free Local Towing :</b> We will pick up your boat donation, running or not, when it's most convenient.</li>
    <li><span class="arrow-dot"><svg width="12" height="12" viewBox="0 0 12 12"><path d="M1 6h9M6 2l4 4-4 4" stroke="#fff" stroke-width="2" fill="none"/></svg></span><b>All Boats Accepted :</b> We take your car regardless of its condition or registration status.</li>
    <li><span class="arrow-dot"><svg width="12" height="12" viewBox="0 0 12 12"><path d="M1 6h9M6 2l4 4-4 4" stroke="#fff" stroke-width="2" fill="none"/></svg></span><b>Income Tax Deduction :</b> We issue you an IRS tax receipt &amp; offer the largest resale network to get you the highest tax write-off possible.</li>
    <li><span class="arrow-dot"><svg width="12" height="12" viewBox="0 0 12 12"><path d="M1 6h9M6 2l4 4-4 4" stroke="#fff" stroke-width="2" fill="none"/></svg></span><b>No Paperwork Hassles :</b> We take any boat and handle everything: DMV, Smog and IRS paperwork.</li>
    <li><span class="arrow-dot"><svg width="12" height="12" viewBox="0 0 12 12"><path d="M1 6h9M6 2l4 4-4 4" stroke="#fff" stroke-width="2" fill="none"/></svg></span><b>Boat donations help fund programs :</b> And benefit National Veterans Outreach Fund. An IRS 501(c)3 nonprofit organization.</li>
    <li><span class="arrow-dot"><svg width="12" height="12" viewBox="0 0 12 12"><path d="M1 6h9M6 2l4 4-4 4" stroke="#fff" stroke-width="2" fill="none"/></svg></span><b>Schedule a Free Pickup :</b> Complete the form and a representative will call you to arrange a convenient time to pickup your boat.</li>
  </ul>
</section>

<section id="faq">
  <span class="title-rule" style="left:255px;top:1665px;width:90px"></span>
  <h2 class="section-title" style="top:1628px">FREQUENTLY ASKED <span>QUESTIONS</span></h2>
  <span class="title-rule" style="left:855px;top:1665px;width:90px"></span>
  <div class="faq-visual" role="img" aria-label="Photo of an American flag waving over marching soldiers' boots"></div>
  <div class="faq-list">
    <div class="faq-item" style="top:0"><div class="q">What types of boats can be donated?<svg width="12" height="8" viewBox="0 0 12 8"><path d="M1 1l5 5 5-5" stroke="#333" stroke-width="2" fill="none"/></svg></div></div>
    <div class="faq-item" style="top:50px;height:132px"><div class="q">What paperwork do I need to donate my boat?<svg width="12" height="8" viewBox="0 0 12 8"><path d="M1 7l5-5 5 5" stroke="#333" stroke-width="2" fill="none"/></svg></div>
      <div class="a">All you need is a title, free of all liens. We will request some general information from you at the time of donation such as, the year, make, and model of the boat, as well as its general mechanical condition. We accept all boats, running or non-running.</div></div>
    <div class="faq-item" style="top:196px"><div class="q">Is my donated boat tax -deductible?<svg width="12" height="8" viewBox="0 0 12 8"><path d="M1 1l5 5 5-5" stroke="#333" stroke-width="2" fill="none"/></svg></div></div>
    <div class="faq-item" style="top:244px"><div class="q">What if the boat is not registered in my name?<svg width="12" height="8" viewBox="0 0 12 8"><path d="M1 1l5 5 5-5" stroke="#333" stroke-width="2" fill="none"/></svg></div></div>
    <div class="faq-item" style="top:292px"><div class="q">How much will I receive as a tax deduction for my boat?<svg width="12" height="8" viewBox="0 0 12 8"><path d="M1 1l5 5 5-5" stroke="#333" stroke-width="2" fill="none"/></svg></div></div>
    <div class="faq-item" style="top:340px"><div class="q">When will I receive my tax receipt?<svg width="12" height="8" viewBox="0 0 12 8"><path d="M1 1l5 5 5-5" stroke="#333" stroke-width="2" fill="none"/></svg></div></div>
    <div class="faq-item" style="top:388px"><div class="q">How do I schedule a pick up?<svg width="12" height="8" viewBox="0 0 12 8"><path d="M1 1l5 5 5-5" stroke="#333" stroke-width="2" fill="none"/></svg></div></div>
  </div>
</section>

<footer class="site-footer" id="about">
  <div class="footer-tab"></div>
  <div class="footer-brand"><span class="brand-dot"></span><span class="brand-name">HULLS FOR HEROES</span></div>
  <div class="footer-col" style="left:72px">
    <h4>ABOUT HULLS FOR HEROES</h4>
    <p>Lorem ipsum dolor sit amet, consectetuer adipiscing elit, sed diam nonummy nibheu ismod tincidunt ut laoreet dolore magna aliquam erat volutpat. Ut wisi enim ad mini veniam, quis nostrud exerci tation ullamcor per suscipit lobortis nisl ut aliquip ex ea co modo consequat.</p>
  </div>
  <div class="footer-col" style="left:382px">
    <h4>NAVIGATION</h4>
    <a href="#how">HOW TO DONATE</a><a href="#why">WHY DONATE</a><a href="#faq">FAQ</a><a href="#about">ABOUT</a>
  </div>
  <div class="footer-col" style="left:556px">
    <h4>SAFE &amp; SECURE</h4>
    <div class="seal" style="width:150px;height:44px"></div>
    <div class="seal" style="width:118px;height:38px"></div>
    <div class="seal" style="width:52px;height:52px;border-radius:50%"></div>
  </div>
  <a class="footer-call" href="tel:18005550142">
    <span class="call-icon"><svg width="34" height="34" viewBox="0 0 24 24"><path fill="#fff" d="M6.6 10.8c1.4 2.8 3.8 5.1 6.6 6.6l2.2-2.2c.3-.3.7-.4 1-.2 1.1.4 2.3.6 3.6.6.6 0 1 .4 1 1V20c0 .6-.4 1-1 1C10.6 21 3 13.4 3 4c0-.6.4-1 1-1h3.5c.6 0 1 .4 1 1 0 1.3.2 2.5.6 3.6.1.3 0 .7-.2 1z"/></svg></span>
    <span class="call-text"><span class="label">CALL TODAY TO DONATE</span><br><span class="number">1-800-555-0142</span><br><span class="hours">Live Operators Available - 7 Days A Week</span></span>
  </a>
</footer>

<div class="copyright">COPYRIGHT © 2017 HULLS FOR HEROES. PRIVACY POLICY I TERMS &amp; CONDITIONS. ALL RIGHTS RESERVED.</div>

</body>
</html>
```